Step and Repeat Backdrop for wedding reception photo booth

Would like to have a Step and Repeat Backdrop (8 foot high by 10 foot wide) that incorporates the wedding logo (attached) and the names Helen and Gavin. Background should be white, and wedding colors are burgundy and gold. Show me creativity :-) I have included some random samples.

```html
<!DOCTYPE html>
<html lang="en">
<head>
<meta charset="utf-8">
<title>Helen &amp; Gavin – Step and Repeat Backdrop</title>
<link href="https://fonts.googleapis.com/css2?family=Libre+Baskerville:wght@700&family=Playfair+Display:ital,wght@1,400&display=swap" rel="stylesheet">
<style>
  :root {
    --page: #e9e8e6;
    --backdrop: #ffffff;
    --gold: #9a7f48;
    --burgundy: #7b0a27;
    --ornament-soft: #f4e9ec;
  }
  html, body {
    margin: 0;
    padding: 0;
    width: 1200px;
    height: 1200px;
    overflow: hidden;
    background: var(--page);
  }
  .backdrop {
    position: absolute;
    left: 40px;
    top: 133px;
    width: 1120px;
    height: 933px;
    background: var(--backdrop);
    box-shadow: 0 2px 10px rgba(0,0,0,0.12);
  }
  .tile {
    position: absolute;
    transform: translate(-50%, -50%);
    white-space: nowrap;
  }
  .names {
    font-family: "Libre Baskerville", "Times New Roman", serif;
    font-weight: 700;
    color: var(--gold);
    font-size: 16px;
    line-height: 1;
    letter-spacing: 0.3px;
  }
  .names .bride { display: block; }
  .names .amp {
    font-family: "Playfair Display", Georgia, serif;
    font-style: italic;
    font-weight: 400;
    font-size: 36px;
    line-height: 0;
    margin-left: 4px;
    position: relative;
    top: 1px;
  }
  .names .groom {
    display: block;
    margin-left: 52px;
    margin-top: 6px;
  }
  .couple-mark {
    font-family: "Libre Baskerville", "Times New Roman", serif;
    font-weight: 700;
    color: var(--burgundy);
    font-size: 13px;
    line-height: 1.35;
    letter-spacing: 0.5px;
    text-align: center;
  }
  .couple-mark span { display: block; }
  .feature-ornament {
    position: absolute;
    left: 385px;
    top: 288px;
    width: 346px;
    height: 359px;
    background: radial-gradient(ellipse at center, #ffffff 45%, var(--ornament-soft) 100%);
  }
  .feature-mark {
    position: absolute;
    left: 558px;
    top: 468px;
    transform: translate(-50%, -50%);
    font-family: "Libre Baskerville", "Times New Roman", serif;
    font-weight: 700;
    color: var(--gold);
    font-size: 44px;
    line-height: 1.25;
    letter-spacing: 1px;
    text-align: center;
    white-space: nowrap;
  }
  .feature-mark span { display: block; }
</style>
</head>
<body>
<div class="backdrop">
  <div class="feature-ornament" role="img" aria-label="Burgundy flourish ornament framing the couple's wedding mark"></div>
  <div class="feature-mark"><span>HELEN &amp;</span><span>GAVIN</span></div>

  <!-- row 1 -->
  <div class="tile names" style="left:90px;top:72px"><span class="bride">HELEN<span class="amp">&amp;</span></span><span class="groom">GAVIN</span></div>
  <div class="tile couple-mark" style="left:248px;top:72px"><span>HELEN &amp;</span><span>GAVIN</span></div>
  <div class="tile names" style="left:416px;top:72px"><span class="bride">HELEN<span class="amp">&amp;</span></span><span class="groom">GAVIN</span></div>
  <div class="tile couple-mark" style="left:573px;top:72px"><span>HELEN &amp;</span><span>GAVIN</span></div>
  <div class="tile names" style="left:740px;top:72px"><span class="bride">HELEN<span class="amp">&amp;</span></span><span class="groom">GAVIN</span></div>
  <div class="tile couple-mark" style="left:897px;top:72px"><span>HELEN &amp;</span><span>GAVIN</span></div>
  <div class="tile names" style="left:1038px;top:72px"><span class="bride">HELEN<span class="amp">&amp;</span></span><span class="groom">GAVIN</span></div>

  <!-- row 2 -->
  <div class="tile couple-mark" style="left:88px;top:188px"><span>HELEN &amp;</span><span>GAVIN</span></div>
  <div class="tile names" style="left:256px;top:188px"><span class="bride">HELEN<span class="amp">&amp;</span></span><span class="groom">GAVIN</span></div>
  <div class="tile couple-mark" style="left:413px;top:188px"><span>HELEN &amp;</span><span>GAVIN</span></div>
  <div class="tile names" style="left:580px;top:188px"><span class="bride">HELEN<span class="amp">&amp;</span></span><span class="groom">GAVIN</span></div>
  <div class="tile couple-mark" style="left:737px;top:188px"><span>HELEN &amp;</span><span>GAVIN</span></div>
  <div class="tile names" style="left:878px;top:188px"><span class="bride">HELEN<span class="amp">&amp;</span></span><span class="groom">GAVIN</span></div>
  <div class="tile couple-mark" style="left:1039px;top:188px"><span>HELEN &amp;</span><span>GAVIN</span></div>

  <!-- row 3 -->
  <div class="tile names" style="left:90px;top:283px"><span class="bride">HELEN<span class="amp">&amp;</span></span><span class="groom">GAVIN</span></div>
  <div class="tile couple-mark" style="left:248px;top:283px"><span>HELEN &amp;</span><span>GAVIN</span></div>
  <div class="tile names" style="left:416px;top:265px"><span class="bride">HELEN<span class="amp">&amp;</span></span><span class="groom">GAVIN</span></div>
  <div class="tile names" style="left:740px;top:272px"><span class="bride">HELEN<span class="amp">&amp;</span></span><span class="groom">GAVIN</span></div>
  <div class="tile couple-mark" style="left:897px;top:283px"><span>HELEN &amp;</span><span>GAVIN</span></div>
  <div class="tile names" style="left:1038px;top:283px"><span class="bride">HELEN<span class="amp">&amp;</span></span><span class="groom">GAVIN</span></div>

  <!-- row 4 -->
  <div class="tile couple-mark" style="left:88px;top:417px"><span>HELEN &amp;</span><span>GAVIN</span></div>
  <div class="tile names" style="left:256px;top:417px"><span class="bride">HELEN<span class="amp">&amp;</span></span><span class="groom">GAVIN</span></div>
  <div class="tile names" style="left:878px;top:417px"><span class="bride">HELEN<span class="amp">&amp;</span></span><span class="groom">GAVIN</span></div>
  <div class="tile couple-mark" style="left:1039px;top:417px"><span>HELEN &amp;</span><span>GAVIN</span></div>

  <!-- row 5 -->
  <div class="tile names" style="left:117px;top:516px"><span class="bride">HELEN<span class="amp">&amp;</span></span><span class="groom">GAVIN</span></div>
  <div class="tile couple-mark" style="left:275px;top:516px"><span>HELEN &amp;</span><span>GAVIN</span></div>
  <div class="tile couple-mark" style="left:856px;top:516px"><span>HELEN &amp;</span><span>GAVIN</span></div>
  <div class="tile names" style="left:995px;top:516px"><span class="bride">HELEN<span class="amp">&amp;</span></span><span class="groom">GAVIN</span></div>

  <!-- row 6 -->
  <div class="tile couple-mark" style="left:88px;top:646px"><span>HELEN &amp;</span><span>GAVIN</span></div>
  <div class="tile names" style="left:256px;top:646px"><span class="bride">HELEN<span class="amp">&amp;</span></span><span class="groom">GAVIN</span></div>
  <div class="tile couple-mark" style="left:413px;top:660px"><span>HELEN &amp;</span><span>GAVIN</span></div>
  <div class="tile couple-mark" style="left:737px;top:660px"><span>HELEN &amp;</span><span>GAVIN</span></div>
  <div class="tile names" style="left:878px;top:646px"><span class="bride">HELEN<span class="amp">&amp;</span></span><span class="groom">GAVIN</span></div>
  <div class="tile couple-mark" style="left:1039px;top:646px"><span>HELEN &amp;</span><span>GAVIN</span></div>

  <!-- row 7 -->
  <div class="tile names" style="left:90px;top:745px"><span class="bride">HELEN<span class="amp">&amp;</span></span><span class="groom">GAVIN</span></div>
  <div class="tile couple-mark" style="left:248px;top:745px"><span>HELEN &amp;</span><span>GAVIN</span></div>
  <div class="tile names" style="left:416px;top:745px"><span class="bride">HELEN<span class="amp">&amp;</span></span><span class="groom">GAVIN</span></div>
  <div class="tile couple-mark" style="left:573px;top:745px"><span>HELEN &amp;</span><span>GAVIN</span></div>
  <div class="tile names" style="left:740px;top:745px"><span class="bride">HELEN<span class="amp">&amp;</span></span><span class="groom">GAVIN</span></div>
  <div class="tile couple-mark" style="left:897px;top:745px"><span>HELEN &amp;</span><span>GAVIN</span></div>
  <div class="tile names" style="left:1038px;top:745px"><span class="bride">HELEN<span class="amp">&amp;</span></span><span class="groom">GAVIN</span></div>

  <!-- row 8 -->
  <div class="tile couple-mark" style="left:88px;top:861px"><span>HELEN &amp;</span><span>GAVIN</span></div>
  <div class="tile names" style="left:256px;top:861px"><span class="bride">HELEN<span class="amp">&amp;</span></span><span class="groom">GAVIN</span></div>
  <div class="tile couple-mark" style="left:413px;top:861px"><span>HELEN &amp;</span><span>GAVIN</span></div>
  <div class="tile names" style="left:580px;top:861px"><span class="bride">HELEN<span class="amp">&amp;</span></span><span class="groom">GAVIN</span></div>
  <div class="tile couple-mark" style="left:737px;top:861px"><span>HELEN &amp;</span><span>GAVIN</span></div>
  <div class="tile names" style="left:878px;top:861px"><span class="bride">HELEN<span class="amp">&amp;</span></span><span class="groom">GAVIN</span></div>
  <div class="tile couple-mark" style="left:1039px;top:861px"><span>HELEN &amp;</span><span>GAVIN</span></div>
</div>
</body>
</html>
```